New Business Card Design Project

Use the flyer uploaded and website www.brightoakbuilders.com for inspiration.
List Our Services on Backside of business cards
Marcus Delling
Harborline Builders Inc.
Licensed General Contractors
858-471-6093

Contact Information for Business Card

Use the flyer uploaded and website www.brightoakbuilders.com for inspiration. List Our Services on Backside of business cards Marcus Delling Harborline Builders Inc. Licensed General Contractors 858-471-6093

```html
<!DOCTYPE html>
<html lang="en">
<head>
<meta charset="utf-8">
<title>Harborline Builders – Business Cards</title>
<link rel="stylesheet" href="https://fonts.googleapis.com/css2?family=Cinzel:wght@400;600&family=Montserrat:wght@400;500&display=swap">
<style>
  :root {
    --backdrop: #1a1a1b;
    --card: #141415;
    --ink: #f4f4f4;
    --ink-soft: #cfcfcf;
  }
  * { box-sizing: border-box; margin: 0; padding: 0; }
  html, body {
    width: 1200px; height: 912px; overflow: hidden;
    background: var(--backdrop);
  }
  .sheet {
    width: 1200px; height: 912px;
    display: flex; flex-direction: column;
    align-items: center; justify-content: center; gap: 44px;
  }
  .card {
    width: 640px; height: 366px;
    background: var(--card);
    border-radius: 16px;
    box-shadow: 0 18px 40px rgba(0,0,0,.55);
    color: var(--ink);
    position: relative;
  }
  .brand-name {
    font-family: "Cinzel", serif;
    font-weight: 400;
    letter-spacing: .04em;
    color: var(--ink);
    display: flex; align-items: center; gap: 12px;
  }
  .brand-dot {
    width: 12px; height: 12px; border-radius: 50%;
    background: var(--ink);
  }

  /* Back: services */
  .card-back {
    display: flex; flex-direction: column;
    align-items: center; justify-content: center; gap: 56px;
  }
  .card-back .brand-name { font-size: 34px; }
  .services {
    font-family: "Montserrat", sans-serif;
    font-size: 19px; line-height: 1.5;
    text-align: center; color: var(--ink);
  }

  /* Front: contact */
  .card-front { padding: 48px 52px; }
  .card-front .brand-name { font-size: 26px; }
  .person { margin-top: 40px; }
  .person-name {
    font-family: "Cinzel", serif; font-weight: 600;
    font-size: 27px; letter-spacing: .03em;
  }
  .person-role {
    font-family: "Montserrat", sans-serif;
    font-size: 17px; color: var(--ink-soft); margin-top: 2px;
  }
  .contacts { list-style: none; margin-top: 30px; }
  .contacts li {
    font-family: "Montserrat", sans-serif; font-size: 16px;
    display: flex; align-items: center; gap: 12px;
    margin-bottom: 10px;
  }
  .contacts svg { width: 16px; height: 16px; flex: none; }
</style>
</head>
<body>
<main class="sheet">
  <section class="card card-back" aria-label="Card back: services">
    <div class="brand-name"><span class="brand-dot"></span>Harborline Builders</div>
    <p class="services">
      Painting • Flooring • Kitchens • Custom Renovations<br>
      Bathrooms • Energy Efficient Upgrades
    </p>
  </section>

  <section class="card card-front" aria-label="Card front: contact">
    <div class="brand-name"><span class="brand-dot"></span>Harborline Builders</div>
    <div class="person">
      <h1 class="person-name">MARCUS DELLING</h1>
      <p class="person-role">Licensed General Contractors</p>
    </div>
    <ul class="contacts">
      <li>
        <svg viewBox="0 0 16 16" aria-hidden="true"><circle cx="8" cy="8" r="8" fill="#f4f4f4"/><path d="M5 4.5l1.6 0 .6 2-1 .8a5 5 0 0 0 2.5 2.5l.8-1 2 .6v1.6c0 .5-.5.9-1 .8A7 7 0 0 1 4.2 5.5c0-.5.3-1 .8-1z" fill="#141415"/></svg>
        858-471-6093
      </li>
      <li>
        <svg viewBox="0 0 16 16" aria-hidden="true"><rect x="1" y="3.5" width="14" height="9" rx="1" fill="#f4f4f4"/><path d="M1.5 4l6.5 5 6.5-5" fill="none" stroke="#141415" stroke-width="1.2"/></svg>
        info@brightoakbuilders.com
      </li>
      <li>
        <svg viewBox="0 0 16 16" aria-hidden="true"><circle cx="8" cy="8" r="7.5" fill="#f4f4f4"/><path d="M8 .5v15M.5 8h15M8 .5c-4 4-4 11 0 15M8 .5c4 4 4 11 0 15" fill="none" stroke="#141415" stroke-width="1"/></svg>
        www.brightoakbuilders.com
      </li>
    </ul>
  </section>
</main>
</body>
</html>
```